Finding the Root: Reason in Clinical Choice-Crafting

I'd like a cover that looks like it would fit on the shelf next to "The Illness Mirage" by Corwin Talley, "The Close of Forgetting" by Hugh Marchetti, "Meal Mend" by Paul Grieve, "The Energy Restart Plan" by Oscar Pemberley or "The Gland Restart Plan" by the same or "The Cortex Restart Plan" by the same ... either text only (with some interesting fonts that make the title stand out, and the subtitle smaller) or a relevant image, though I'm not entirely sure what that would be since this is a book about big-picture medical decision making.
Author name is Dr Tessa Morrow, NMD
I'll eventually request an e-book, paperback, and audio cover from the winner...

Target Market(s)

practicing physicians

Industry/Entity Type

medicine

Requirements
Must have
• look similar to other books in the genre

```html
<!DOCTYPE html>
<html lang="en">
<head>
<meta charset="utf-8">
<title>Finding the Root: Reason in Clinical Choice-Crafting — Book Cover</title>
<link rel="stylesheet" href="https://fonts.googleapis.com/css2?family=Bebas+Neue&display=swap">
<style>
  :root {
    --backdrop: #9b9b9b;
    --paper: #ffffff;
    --ink-teal: #1f3c42;
    --accent-yellow: #e9d41d;
    --pale-yellow: #f8f0b4;
  }
  html, body {
    margin: 0;
    padding: 0;
    width: 1200px;
    height: 2595px;
    overflow: hidden;
    background: var(--backdrop);
  }
  .book-cover {
    position: absolute;
    left: 60px;
    top: 490px;
    width: 1080px;
    height: 1607px;
    box-shadow: 0 24px 40px rgba(0, 0, 0, 0.28);
  }
  .book-cover svg { display: block; }
  .cover-type { font-family: "Bebas Neue", "Oswald", sans-serif; }
  .fill-paper { fill: var(--paper); }
  .fill-teal { fill: var(--ink-teal); }
  .fill-yellow { fill: var(--accent-yellow); }
  .tone-core { stop-color: var(--pale-yellow); }
  .tone-edge { stop-color: var(--paper); }
</style>
</head>
<body>
  <main class="book-cover">
    <svg width="1080" height="1607" viewBox="0 0 1080 1607" xmlns="http://www.w3.org/2000/svg">
      <defs>
        <radialGradient id="tangle-tone" cx="50%" cy="48%" r="52%">
          <stop offset="0" class="tone-core"/>
          <stop offset="0.7" class="tone-core" stop-opacity="0.6"/>
          <stop offset="1" class="tone-edge"/>
        </radialGradient>
      </defs>

      <!-- upper white field -->
      <rect class="fill-paper" x="0" y="0" width="1080" height="996"/>

      <!-- artwork area: tangled thread unravelling into an arrow -->
      <rect class="tangle-art" x="300" y="70" width="780" height="440"
            fill="url(#tangle-tone)" role="img"
            aria-label="Yellow line drawing of a tangled thread that unravels into a single arrow pointing at the title"/>

      <!-- title -->
      <g class="cover-type title-block">
        <text class="fill-teal title-lead" x="77" y="248" font-size="234" textLength="566" lengthAdjust="spacingAndGlyphs">FINDING</text>
        <text class="fill-teal title-lead" x="77" y="486" font-size="234" textLength="200" lengthAdjust="spacingAndGlyphs">THE</text>
        <text class="fill-teal title-hero" x="89" y="996" font-size="664" textLength="904" lengthAdjust="spacingAndGlyphs">ROOT</text>
      </g>

      <!-- lower teal band -->
      <rect class="fill-teal" x="0" y="996" width="1080" height="611"/>

      <g class="cover-type subtitle-block">
        <text class="fill-paper subtitle-lead" x="91" y="1247" font-size="96" textLength="238" lengthAdjust="spacingAndGlyphs">REASON IN</text>
        <text class="fill-yellow subtitle-key" x="352" y="1247" font-size="252" textLength="646" lengthAdjust="spacingAndGlyphs">CLINICAL</text>
        <text class="fill-paper subtitle-tail" x="89" y="1326" font-size="53" textLength="569" lengthAdjust="spacing">CHOICE-CRAFTING</text>
      </g>

      <text class="cover-type author-name" x="90" y="1482" font-size="67" textLength="593" lengthAdjust="spacing"><tspan class="fill-yellow">DR TESSA MORROW,</tspan><tspan class="fill-paper"> NMD</tspan></text>
    </svg>
  </main>
</body>
</html>
```